KLV Plant Services

We are a heavy diesel mechanical business with additional air con certificates, remapping engine rebuilt

Contact Information for Business Card

Company Name, Director Name, Managing Director, Contact details, email and website

Font styles to use
Serif
Script

```html
<!DOCTYPE html>
<html lang="en">
<head>
<meta charset="utf-8">
<title>KLV Plant Services — Business Card</title>
<link rel="stylesheet" href="https://fonts.googleapis.com/css2?family=Montserrat:wght@700&family=Poppins:wght@300;400;700&display=swap">
<style>
  :root {
    --navy: #0b0a6e;
    --navy-edge: #1a1a9c;
    --ink: #0a0a0a;
    --paper: #ffffff;
    --stage: #2a2a2a;
    --back-card: #121212;
    --back-sheen: #1e1e1e;
    --text: #1b1b1b;
  }
  * { margin: 0; padding: 0; box-sizing: border-box; }
  html, body { width: 1200px; height: 881px; overflow: hidden; }
  body {
    background: var(--stage);
    font-family: "Poppins", sans-serif;
    display: flex;
    align-items: center;
    justify-content: center;
    gap: 48px;
  }
  .card {
    position: relative;
    width: 540px;
    height: 310px;
    border-radius: 4px 22px 4px 22px;
    overflow: hidden;
    box-shadow: 0 4px 0 var(--navy-edge), 0 18px 30px rgba(0,0,0,.45);
  }
  .card-back {
    background: linear-gradient(160deg, var(--back-sheen), var(--back-card) 60%);
  }
  .card-back .pattern-area { position: absolute; inset: 0; }
  .card-front { background: var(--paper); }
  .card-front .waves { position: absolute; inset: 0; }
  .holder {
    position: absolute;
    right: 26px;
    top: 26px;
    text-align: right;
    color: var(--paper);
  }
  .holder-name {
    font-family: "Montserrat", sans-serif;
    font-weight: 700;
    font-size: 23px;
    letter-spacing: 1.5px;
    line-height: 1;
  }
  .holder-role {
    font-weight: 300;
    font-size: 12px;
    letter-spacing: .5px;
    margin-top: 2px;
  }
  .brand {
    position: absolute;
    left: 44px;
    bottom: 62px;
    color: var(--navy);
    font-weight: 700;
    line-height: .95;
  }
  .brand-initials { font-size: 62px; letter-spacing: 2px; }
  .brand-tail { font-size: 21px; }
  .contact {
    position: absolute;
    right: 22px;
    top: 160px;
    text-align: right;
    color: var(--text);
    font-weight: 300;
    font-size: 13px;
    line-height: 1.3;
    list-style: none;
  }
  .contact .address { margin-bottom: 8px; }
  .contact li { display: flex; align-items: center; justify-content: flex-end; gap: 6px; }
  .contact li.address { display: block; padding-right: 18px; }
  .contact svg { width: 12px; height: 12px; flex: none; }
</style>
</head>
<body>
  <section class="card card-back">
    <div class="pattern-area" role="img" aria-label="Repeating tone-on-tone company mark pattern across the back of the card"></div>
  </section>

  <section class="card card-front">
    <svg class="waves" viewBox="0 0 540 310" preserveAspectRatio="none" aria-hidden="true">
      <path d="M0,0 H540 V100 C420,140 220,62 0,60 Z" fill="var(--navy)"/>
      <path d="M0,64 C200,62 400,150 540,104 L540,112 C400,150 200,76 0,70 Z" fill="var(--ink)"/>
      <path d="M0,70 C200,76 400,150 540,112 L540,118 C400,152 200,84 0,76 Z" fill="var(--paper)"/>
      <rect x="0" y="302" width="540" height="8" fill="var(--navy)"/>
    </svg>

    <header class="holder">
      <p class="holder-name">MARK ELLISON</p>
      <p class="holder-role">Director</p>
    </header>

    <p class="brand">
      <span class="brand-initials">KLV</span><br>
      <span class="brand-tail">Plant Services</span>
    </p>

    <ul class="contact">
      <li class="address">2750 Harlow Rd Millbrook<br>GA 30112</li>
      <li>470-555-0148
        <svg viewBox="0 0 24 24"><path d="M6.6 10.8a15.2 15.2 0 0 0 6.6 6.6l2.2-2.2a1 1 0 0 1 1-.25 11.4 11.4 0 0 0 3.6.57 1 1 0 0 1 1 1V20a1 1 0 0 1-1 1A17 17 0 0 1 3 4a1 1 0 0 1 1-1h3.5a1 1 0 0 1 1 1c0 1.25.2 2.45.57 3.57a1 1 0 0 1-.25 1z" fill="var(--navy)"/></svg>
      </li>
      <li>info@klvplantservices.com
        <svg viewBox="0 0 24 24"><rect x="3" y="5" width="18" height="14" rx="1.5" fill="none" stroke="var(--navy)" stroke-width="2"/><path d="M3 6l9 7 9-7" fill="none" stroke="var(--navy)" stroke-width="2"/></svg>
      </li>
      <li>www.klvplantservices.com
        <svg viewBox="0 0 24 24"><circle cx="12" cy="12" r="9" fill="none" stroke="var(--navy)" stroke-width="2"/><path d="M3 12h18M12 3c3 3.5 3 14.5 0 18M12 3c-3 3.5-3 14.5 0 18" fill="none" stroke="var(--navy)" stroke-width="1.6"/></svg>
      </li>
    </ul>
  </section>
</body>
</html>
```